Best local air conditioning and heating contractor

We need a website design for a new company in Tampa Bay called the Coastal Breeze Cooling Company. We provide superior services for residential and commercial properties as well as maintenance and installing HVAC systems. We also want to sell equipment, parts and filter on the website as well. We want it easy to use for customers. Rich with content and keywords for our area.

Target Market(s)

homeowners in Tampa Bay

Industry/Entity Type

HVAC air conditioning and heating

Coding

Coded - Design and coding required

Number of Pages Required

5+ page

Font styles to use
Sans Serif

Requirements
Nice to have
• would like the colors to be same as logo

```html
<!DOCTYPE html>
<html lang="en">
<head>
<meta charset="utf-8">
<title>Coastal Breeze Cooling Company</title>
<link href="https://fonts.googleapis.com/css2?family=Exo+2:wght@600;700&family=Roboto:wght@400;500;700&display=swap" rel="stylesheet">
<style>
:root{
  --navy:#22306b;
  --navy-dark:#1d2a62;
  --red:#d71f26;
  --red-bg:#d52027;
  --ink:#222;
  --muted:#777;
  --light:#f3f5f8;
  --white:#fff;
}
*{box-sizing:border-box;margin:0;padding:0}
html,body{width:1200px;height:4728px;overflow:hidden}
body{font-family:"Roboto",Arial,sans-serif;color:var(--ink);background:var(--white);position:relative}
.abs{position:absolute}
.heading{font-family:"Exo 2",Arial,sans-serif;font-weight:700;color:var(--navy)}
.btn{display:inline-block;background:var(--red);color:#fff;font:700 12px "Roboto",sans-serif;border-radius:4px;text-align:center}

/* header */
.header{top:0;left:0;width:1200px;height:138px;background:#fff}
.brand{left:110px;top:34px;display:flex;align-items:center;gap:10px}
.brand-dot{width:30px;height:30px;border-radius:50%;background:var(--red)}
.brand-name{font:700 21px/1.1 "Exo 2",sans-serif;color:var(--navy);width:210px}
.info{display:flex;align-items:center;gap:16px}
.info-icon{width:54px;height:54px;border-radius:50%;background:var(--red);border:4px solid #f6d0d1;display:flex;align-items:center;justify-content:center}
.info small{display:block;font-size:10px;color:#444;margin-bottom:6px}
.info strong{font-size:18px;font-weight:500;color:#111}
.info.hours strong{font-size:13px}
.reviews{left:992px;top:24px;font-size:10px;color:#555;line-height:1.6}
.stars{color:var(--red);font-size:11px;letter-spacing:1px}
.nav{left:372px;top:95px;width:740px;height:43px;background:var(--navy);clip-path:polygon(20px 0,100% 0,100% 100%,0 100%)}
.nav ul{list-style:none;display:flex;position:absolute;left:44px;top:14px;gap:0}
.nav li{color:#fff;font-size:13px;margin-right:44px}
.nav-social{right:0;top:0;width:175px;height:43px;background:var(--red);clip-path:polygon(20px 0,100% 0,100% 100%,0 100%);display:flex;align-items:center;justify-content:center;gap:12px;padding-left:14px}
.ring{width:24px;height:24px;border-radius:50%;border:1.5px solid #fff}

/* hero */
.hero{top:138px;left:0;width:1200px;height:617px;background:linear-gradient(100deg,#4a4640 0%,#6d6259 40%,#a59a90 70%,#cfc6bd 100%)}
.hero-title{left:110px;top:160px;font:600 60px/1.3 "Exo 2",sans-serif;color:#fff}
.hero-title span{color:var(--red)}
.hero-sub{left:110px;top:405px;font:500 25px "Roboto",sans-serif;color:#fff}
.hero-btn{left:110px;top:462px;width:138px;height:46px;line-height:46px;background:var(--navy);color:#fff;font:700 14px "Roboto",sans-serif;border-radius:4px;text-align:center}

/* about */
.about-frame{left:89px;top:865px;width:534px;height:475px;border:1px solid var(--red)}
.about-photo{left:112px;top:888px;width:533px;height:474px;background:linear-gradient(135deg,#e9e4dc,#8fb0b6 45%,#2f6e7e 70%,#d8d3cb);box-shadow:0 10px 25px rgba(0,0,0,.15)}
.about-text{left:740px;top:912px;width:360px}
.about-text h2{font-size:46px;margin-bottom:22px}
.about-text p{font-size:13px;line-height:31px;color:var(--muted);margin-bottom:31px}
.about-text .btn{width:110px;height:36px;line-height:36px;margin-top:-4px}

/* offer */
.offer{top:1480px;left:0;width:1200px;height:816px;background:var(--light)}
.section-title{left:0;width:1200px;text-align:center;font-size:46px}
.offer-intro{left:200px;top:150px;width:800px;text-align:center;font-size:13px;line-height:32px;color:var(--muted)}
.card{top:242px;width:310px;height:486px;background:#fff;box-shadow:0 4px 14px rgba(0,0,0,.08);text-align:center}
.card-photo{position:absolute;left:6px;top:6px;width:298px;height:232px}
.card-icon{position:absolute;left:119px;top:203px;width:72px;height:72px;border-radius:50%;background:var(--navy);border:4px solid #fff;display:flex;align-items:center;justify-content:center}
.card h3{position:absolute;left:0;top:298px;width:100%;font:500 20px "Roboto",sans-serif;color:var(--navy)}
.card p{position:absolute;top:330px;left:25px;width:260px;font-size:12.5px;line-height:26px;color:var(--muted)}
.card .btn{position:absolute;left:100px;top:418px;width:110px;height:36px;line-height:36px}

/* products */
.banner{left:112px;top:2480px;width:976px;height:372px;border-radius:6px;overflow:hidden;background:linear-gradient(90deg,#e7e4e1 0%,#cfcac8 30%,#22306b 58%,#22306b 100%)}
.banner-text{left:705px;top:2564px;width:330px;color:#fff}
.banner-text h3{font:500 27px "Roboto",sans-serif;margin-bottom:14px}
.banner-text p{font-size:13px;line-height:28px;padding-left:6px}
.banner-text .btn{margin:14px 0 0 6px;width:146px;height:36px;line-height:36px}
.product{top:2882px;width:315px;height:308px;background:#fff;box-shadow:0 4px 14px rgba(0,0,0,.08);text-align:center}
.product-photo{position:absolute;left:30px;top:20px;width:255px;height:220px;border-radius:4px}
.product span{position:absolute;top:262px;left:0;width:100%;font:700 17px "Roboto",sans-serif;color:#222}

/* why */
.why{top:3308px;left:0;width:1200px;height:422px;background:linear-gradient(120deg,#d52027,#c81d24 60%,#d52027)}
.why .section-title{color:#fff;top:70px;position:absolute}
.stat{top:160px;width:232px;height:180px;border:1px solid rgba(255,255,255,.8);border-radius:8px;text-align:center;color:#fff}
.stat-num{position:absolute;left:77px;top:28px;width:76px;height:76px;border-radius:50%;background:#fff;color:var(--red);font:700 28px/76px "Exo 2",sans-serif}
.stat-label{position:absolute;left:0;top:128px;width:100%;text-align:center;font-size:16px;color:#fff}

/* contact */
.field{left:207px;width:374px;height:60px;background:#fff;box-shadow:0 2px 14px rgba(0,0,0,.08);font-size:13px;color:#777;padding:20px 27px}
.message{left:619px;top:3915px;width:374px;height:293px;background:#fff;box-shadow:0 2px 14px rgba(0,0,0,.08);font-size:13px;color:#777;padding:20px 27px}
.submit{left:207px;top:4148px;width:374px;height:60px;background:var(--red);color:#fff;font:700 14px/60px "Roboto",sans-serif;text-align:center}

/* footer */
.tools{top:4285px;left:0;width:1200px;height:173px;background:linear-gradient(180deg,#e8e8ea,#b9bcc2 55%,#6b6f78)}
.footer{top:4458px;left:0;width:1200px;height:270px;background:var(--navy);color:#fff}
.foot-info{left:0;top:60px;width:1200px;display:flex;justify-content:center;gap:48px;font-size:13px}
.foot-info div{display:flex;align-items:center;gap:10px}
.foot-links{left:0;top:114px;width:1200px;display:flex;justify-content:center;font-size:13px}
.foot-links span{padding:0 38px;border-right:1px solid #fff}
.foot-links span:last-child{border-right:none}
.foot-rule{top:157px;left:0;width:1200px;height:1px;background:rgba(255,255,255,.25)}
.foot-social{left:0;top:178px;width:1200px;display:flex;justify-content:center;gap:12px}
.copyright{left:0;top:224px;width:1200px;text-align:center;font-size:13px}
.copyright em{font-style:normal;color:var(--red)}
</style>
</head>
<body>

<header class="abs header">
  <div class="abs brand"><div class="brand-dot"></div><div class="brand-name">Coastal Breeze Cooling Company</div></div>
  <div class="abs info" style="left:440px;top:18px">
    <div class="info-icon"><svg width="20" height="20" viewBox="0 0 24 24"><path fill="#fff" d="M6.6 10.8a15 15 0 006.6 6.6l2.2-2.2a1 1 0 011-.3 11 11 0 003.6.6 1 1 0 011 1V20a1 1 0 01-1 1A17 17 0 013 4a1 1 0 011-1h3.5a1 1 0 011 1c0 1.3.2 2.5.6 3.6a1 1 0 01-.3 1z"/></svg></div>
    <div><small>Call Now:</small><strong>+1 813 555 0142</strong></div>
  </div>
  <div class="abs info hours" style="left:745px;top:18px">
    <div class="info-icon"><svg width="20" height="20" viewBox="0 0 24 24" fill="none" stroke="#fff" stroke-width="2"><circle cx="12" cy="12" r="9"/><path d="M12 7v5l3 2"/></svg></div>
    <div><small>Opening Hours:</small><strong>9 AM to 6PM</strong></div>
  </div>
  <div class="abs reviews"><div class="stars">★★★★☆</div>450+ 5 Star Reviews<br>Verified</div>
  <nav class="abs nav">
    <ul><li>Home</li><li>About Us</li><li>Our Services</li><li>Testimonials</li><li>Contact Us</li></ul>
    <div class="abs nav-social"><div class="ring"></div><div class="ring"></div><div class="ring"></div></div>
  </nav>
</header>

<section class="abs hero" role="img" aria-label="Family relaxing on a sofa under a wall-mounted air conditioner">
  <h1 class="abs hero-title">The Coastal <span>Breeze<br>Cooling</span><br>Company</h1>
  <p class="abs hero-sub">SERVICES BEYOND COMPARISON</p>
  <span class="abs hero-btn">GET STARTED</span>
</section>

<div class="abs about-frame"></div>
<div class="abs about-photo" role="img" aria-label="Technicians servicing an indoor air conditioning unit"></div>
<section class="abs about-text">
  <h2 class="heading">About Us</h2>
  <p>Sed ut perspiciatis unde omnis iste natus error sit voluptatem accusantium doloremque laudantium, totam rem aperiam, eaque ipsa quae ab illo inventore veritatis et quasi architecto beatae vitae dicta sunt explicabo.</p>
  <p>Nemo enim ipsam voluptatem quia voluptas sit aspernatur aut odit aut fugit, sed quia consequuntur magni dolores eos qui ratione</p>
  <span class="btn">Read More</span>
</section>

<section class="abs offer">
  <h2 class="abs heading section-title" style="top:80px">What We Offer</h2>
  <p class="abs offer-intro">Sed ut perspiciatis unde omnis iste natus error sit voluptatem accusantium doloremque laudantium, totam rem aperiam, eaque ipsa quae ab illo inventore veritatis et quasi architecto beatae vitae dicta sunt explicabo.</p>

  <article class="abs card" style="left:112px">
    <div class="card-photo" role="img" aria-label="Hands adjusting a wall air conditioner" style="background:linear-gradient(135deg,#f2f3f5,#d9dde3 60%,#3b5ca8)"></div>
    <div class="card-icon"><svg width="34" height="34" viewBox="0 0 34 34" fill="none" stroke="#fff" stroke-width="1.8"><rect x="4" y="9" width="26" height="12" rx="2"/><path d="M8 17h18M11 25v3M17 25v3M23 25v3"/></svg></div>
    <h3>Air Conditioning</h3>
    <p>Sed ut perspiciatis unde omnis iste natus error sit voluptatem accusantium doloremque laudantium, totam rem</p>
    <span class="btn">View Details</span>
  </article>
  <article class="abs card" style="left:444px">
    <div class="card-photo" role="img" aria-label="Technician maintaining an outdoor HVAC unit" style="background:linear-gradient(135deg,#c9c6c0,#6f6a66 55%,#2a3350)"></div>
    <div class="card-icon"><svg width="34" height="34" viewBox="0 0 34 34" fill="none" stroke="#fff" stroke-width="1.8"><circle cx="17" cy="11" r="5"/><path d="M8 29c0-6 4-9 9-9s9 3 9 9"/><path d="M22 22l5-5"/></svg></div>
    <h3>HVAC Maintenance</h3>
    <p>Sed ut perspiciatis unde omnis iste natus error sit voluptatem accusantium doloremque laudantium, totam rem</p>
    <span class="btn">View Details</span>
  </article>
  <article class="abs card" style="left:776px">
    <div class="card-photo" role="img" aria-label="Installers fitting a ceiling HVAC unit" style="background:linear-gradient(135deg,#eceff2,#b9c2cc 50%,#2f6d93)"></div>
    <div class="card-icon"><svg width="34" height="34" viewBox="0 0 34 34" fill="none" stroke="#fff" stroke-width="1.8"><path d="M8 8l18 18M26 8L8 26"/><circle cx="8" cy="8" r="3"/><circle cx="26" cy="26" r="3"/></svg></div>
    <h3>HVAC Installation</h3>
    <p>Sed ut perspiciatis unde omnis iste natus error sit voluptatem accusantium doloremque laudantium, totam rem</p>
    <span class="btn">View Details</span>
  </article>
</section>

<h2 class="abs heading section-title" style="top:2376px">Shop Our Products</h2>
<div class="abs banner" role="img" aria-label="Woman relaxing on a sofa holding an air conditioner remote"></div>
<div class="abs banner-text">
  <h3>Air Conditioning</h3>
  <p>Sed ut perspiciatis unde omnis iste natus error sit voluptatem accusantium doloremque laudantium, totam rem aperiam</p>
  <span class="btn">View All Products</span>
</div>
<div class="abs product" style="left:112px"><div class="product-photo" role="img" aria-label="Split air conditioner indoor and outdoor units" style="background:radial-gradient(circle,#e4e7ec,#fff 70%)"></div><span>Equipment</span></div>
<div class="abs product" style="left:442px"><div class="product-photo" role="img" aria-label="Compressor and radiator parts" style="background:radial-gradient(circle,#b8bcc2,#fff 70%)"></div><span>Parts</span></div>
<div class="abs product" style="left:773px"><div class="product-photo" role="img" aria-label="Pleated air filter" style="background:radial-gradient(circle,#e6e2da,#c9a97d 45%,#fff 72%)"></div><span>Equipment</span></div>

<section class="abs why">
  <h2 class="heading section-title">Why Choose Us</h2>
  <div class="abs stat" style="left:112px"><div class="stat-num">25</div><div class="stat-label">Awards</div></div>
  <div class="abs stat" style="left:360px"><div class="stat-num">95</div><div class="stat-label">Total Review</div></div>
  <div class="abs stat" style="left:608px"><div class="stat-num">75</div><div class="stat-label">Customer's Count</div></div>
  <div class="abs stat" style="left:856px"><div class="stat-num">4.5</div><div class="stat-label">Star Rating</div></div>
</section>

<h2 class="abs heading section-title" style="top:3808px">Get In Touch With Us</h2>
<div class="abs field" style="top:3915px">Full Name</div>
<div class="abs field" style="top:3992px">Email Address</div>
<div class="abs field" style="top:4070px">Contact Number</div>
<div class="abs submit">Submit Here</div>
<div class="abs message">Message</div>

<div class="abs tools" role="img" aria-label="Row of wrenches and plumbing tools"></div>
<footer class="abs footer">
  <div class="abs foot-info">
    <div><svg width="12" height="14" viewBox="0 0 12 16"><path fill="#fff" d="M6 0a6 6 0 016 6c0 4-6 10-6 10S0 10 0 6a6 6 0 016-6zm0 4a2 2 0 100 4 2 2 0 000-4z"/></svg>The Coastal Breeze Cooling Company, Tampa Bay</div>
    <div><svg width="13" height="13" viewBox="0 0 24 24"><path fill="#fff" d="M6.6 10.8a15 15 0 006.6 6.6l2.2-2.2a1 1 0 011-.3 11 11 0 003.6.6 1 1 0 011 1V20a1 1 0 01-1 1A17 17 0 013 4a1 1 0 011-1h3.5a1 1 0 011 1c0 1.3.2 2.5.6 3.6a1 1 0 01-.3 1z"/></svg>+1 813 555 0142</div>
    <div><svg width="14" height="11" viewBox="0 0 16 12"><rect width="16" height="12" rx="1" fill="#fff"/><path d="M1 1l7 6 7-6" stroke="#22306b" fill="none"/></svg>info@coastalbreezecooling.com</div>
  </div>
  <div class="abs foot-links"><span>Home</span><span>About Us</span><span>Our Services</span><span>Testimonials</span><span>Contact Us</span></div>
  <div class="abs foot-rule"></div>
  <div class="abs foot-social"><div class="ring"></div><div class="ring"></div><div class="ring"></div></div>
  <p class="abs copyright">(C) Copyright 2024 <em>The Coastal Breeze Cooling Company</em> | All Rights Reserved</p>
</footer>

</body>
</html>
```